Harbor Crestline (Business Card Design)

Need business cards designed. Something modern, chic, and sleek. Mabye the back of the card should be the navy blue that is in the logo and then just the logo on the back.

Target Market(s)

Those in the hotel, office, and renovation industry

Contact Information for Business Card

1. Logo 2. Dorian Fenwick 3. CEO/Founder 4. Phone: (833) HarbCre / (833) 427-2731 5. Email: dorian@theharborcrestline.com 6. Website: www.theharborcrestline.com

Font styles to use
Other font styles liked:
• Look at the logo font and base the font for everything else off of that.

Colors
0054AA
0677BA
7BADD7
CADEEF
E8F1F8

Requirements
Must have
• Colors that are associated in the logo
Nice to have
• Sleek modern clean and chic design.

```html
<!DOCTYPE html>
<html lang="en">
<head>
<meta charset="utf-8">
<title>Harbor Crestline – Business Card</title>
<link href="https://fonts.googleapis.com/css2?family=Poppins:wght@400;500;600&display=swap" rel="stylesheet">
<style>
  :root {
    --navy: #111a3f;
    --gold: #d4a43c;
    --ink-grey: #5c5c5c;
    --paper: #ffffff;
    --backdrop: #e4e4e4;
  }
  * { margin: 0; padding: 0; box-sizing: border-box; }
  html, body {
    width: 1200px; height: 959px; overflow: hidden;
    background: var(--backdrop);
    font-family: "Poppins", sans-serif;
  }
  .canvas { position: relative; width: 1200px; height: 959px; }
  .card {
    position: absolute; left: 295px; width: 612px; height: 351px;
    box-shadow: 0 2px 6px rgba(0,0,0,.18);
  }
  .card--front { top: 103px; background: var(--paper); }
  .card--back { top: 499px; background: var(--navy); }

  .brand {
    position: absolute; display: flex; flex-direction: column; align-items: center;
    text-align: center; font-weight: 600; text-transform: uppercase;
  }
  .brand__mark { width: 14px; height: 14px; background: var(--gold); margin-bottom: 12px; }
  .brand__name { letter-spacing: 2px; line-height: 1.15; }

  .card--front .brand { left: 60px; width: 185px; top: 118px; color: var(--navy); }
  .card--front .brand__name { font-size: 22px; }

  .divider {
    position: absolute; left: 264px; top: 106px; width: 2px; height: 139px; background: var(--gold);
  }
  .person { position: absolute; left: 285px; top: 97px; }
  .person__name { font-size: 25px; font-weight: 600; color: var(--navy); line-height: 1.2; }
  .person__role { font-size: 15px; font-weight: 400; color: var(--gold); line-height: 1.3; }

  .contacts { position: absolute; left: 285px; top: 184px; list-style: none; }
  .contacts li {
    display: flex; align-items: center; gap: 5px;
    font-size: 15.5px; color: var(--ink-grey); line-height: 22px;
  }
  .contacts svg { width: 13px; height: 13px; flex: none; fill: var(--navy); }

  .card--back .brand { left: 0; right: 0; top: 112px; color: #fff; }
  .card--back .brand__mark { width: 16px; height: 16px; margin-bottom: 16px; }
  .card--back .brand__name { font-size: 28px; letter-spacing: 3px; }
</style>
</head>
<body>
<main class="canvas">
  <section class="card card--front">
    <div class="brand">
      <span class="brand__mark"></span>
      <span class="brand__name">Harbor<br>Crestline</span>
    </div>
    <span class="divider"></span>
    <div class="person">
      <h1 class="person__name">Dorian Fenwick</h1>
      <p class="person__role">CEO/Founder</p>
    </div>
    <ul class="contacts">
      <li><svg viewBox="0 0 24 24"><path d="M6.6 10.8a15.1 15.1 0 0 0 6.6 6.6l2.2-2.2c.3-.3.7-.4 1-.2 1.1.4 2.3.6 3.6.6.6 0 1 .4 1 1V20c0 .6-.4 1-1 1A17 17 0 0 1 3 4c0-.6.4-1 1-1h3.5c.6 0 1 .4 1 1 0 1.3.2 2.5.6 3.6.1.3 0 .7-.2 1l-2.3 2.2z"/></svg>(833) HarbCre / (833) 427-2731</li>
      <li><svg viewBox="0 0 24 24"><path d="M2 5h20v14H2z" fill="var(--navy)"/><path d="M2 5l10 8 10-8M2 19l7-7M22 19l-7-7" stroke="#fff" stroke-width="1.6" fill="none"/></svg>dorian@theharborcrestline.com</li>
      <li><svg viewBox="0 0 24 24" fill="none"><g stroke="var(--navy)" stroke-width="1.8" fill="none"><circle cx="12" cy="12" r="10"/><ellipse cx="12" cy="12" rx="4.5" ry="10"/><path d="M2 12h20M4 7h16M4 17h16"/></g></svg>www.theharborcrestline.com</li>
    </ul>
  </section>

  <section class="card card--back">
    <div class="brand">
      <span class="brand__mark"></span>
      <span class="brand__name">Harbor Crestline</span>
    </div>
  </section>
</main>
</body>
</html>
```